verdant terraces simple classy business card design

my name is colin barrow and I run a gardening business aimed at high class verdant terraces. the business name is verdant terraces and our logo was designed on pixel harbour .My clientel are anything from residential homes to businesses. I take pride in my work and know that I offer a service like no other in my area.
The business card will be used to represent my business and I want it to be not only rememberable, but simplistic and modern. Eye catching too. Of course I would like it relatable to gardening and appealing to the correct clientel - those being garden enthusiasts, prestigious homes and businesses that are after top of the line gardening services like no other on the market.
I am not a typical lawn mowing business so I don't want a typical card design that represents that. The gardens I work with are generally million dollar properties with owners who are very garden proud looking for upkeep and guidance from me along with sometimes whole new garden designs. I want the business cards to show to my clients that I take pride, as they do, in their garden. And I want them to know from my card that I am a professional, qualified horticulturist offering them a top of the line service for life. I want them to refer my business on. I want them to look at my business card and see class and professionalism in a modern unique bold way.
The card should be simple with the possibility of the logo on the front being embossed/debossed and my details on the back the card should have a organic garden feel it's very important to me that it is absolutely perfect
I am also very open to ideas and suggestions so look forward to seeing the designs. the business logo has been supplied with this project and I want the card to be double sided

Contact info is
Colin Barrow - Managing Director / Horticulturist
Phone : 0481 526 704
Email: colinbarrow@verdantterraces.example.au

Target Market(s)

high class gardens residential and commercial

Industry/Entity Type

Gardener

Contact Information for Business Card

Contact info is
Phone : 0481 526 704

PLEASE MAKE CARD DOUBLE SIDED

Requirements
Must have
• organic simple classy modern feel
• must flow with the current logo that has been supplied with this project
• Double sided
• Must explain in a simple way that I deal with high end gardens and I'm a qualified horticulturist
Nice to have
• embossed debossed logo
Should not have
• shouldn't be to busy or cheap looking

```html
<!DOCTYPE html>
<html lang="en">
<head>
<meta charset="utf-8">
<title>Verdant Terraces – Business Card</title>
<link rel="stylesheet" href="https://fonts.googleapis.com/css2?family=Cinzel:wght@500&family=Questrial&display=swap">
<style>
  :root {
    --page-bg: #ecebe7;
    --card-bg: #fbfbf9;
    --leaf-green: #4b9a3c;
    --ink: #2e2e2e;
    --rule: #7fb870;
    --shadow: rgba(60, 50, 40, 0.14);
  }
  * { margin: 0; padding: 0; box-sizing: border-box; }
  html, body {
    width: 1200px;
    height: 794px;
    overflow: hidden;
    background: var(--page-bg);
  }
  .sheet {
    width: 1200px;
    height: 794px;
    display: flex;
    align-items: center;
    justify-content: center;
    gap: 44px;
  }
  .card {
    width: 540px;
    height: 330px;
    background: var(--card-bg);
    box-shadow: 0 6px 18px var(--shadow);
    position: relative;
    display: flex;
    flex-direction: column;
    align-items: center;
  }

  /* Front */
  .card-front { justify-content: center; gap: 16px; }
  .brand-dot {
    width: 70px;
    height: 70px;
    border-radius: 50%;
    background: var(--leaf-green);
  }
  .brand-name {
    font-family: "Cinzel", serif;
    font-weight: 500;
    font-size: 34px;
    letter-spacing: 0.08em;
    color: var(--leaf-green);
    text-transform: uppercase;
  }

  /* Back */
  .card-back { padding-top: 40px; }
  .card-back .brand-dot { width: 78px; height: 78px; }
  .rule {
    width: 360px;
    height: 1px;
    background: var(--rule);
  }
  .rule-top { margin-top: 24px; }
  .rule-bottom { margin-top: 10px; }
  .contact {
    font-family: "Questrial", sans-serif;
    text-align: center;
    margin-top: 8px;
  }
  .contact-name {
    font-size: 21px;
    font-weight: 700;
    color: var(--leaf-green);
    letter-spacing: 0.02em;
  }
  .contact-role {
    font-size: 15px;
    color: var(--ink);
    margin-top: 4px;
  }
  .contact-lines {
    font-size: 13px;
    color: var(--ink);
    margin-top: 10px;
    letter-spacing: 0.02em;
  }
  .contact-lines .label { color: var(--leaf-green); }
  .contact-lines .item + .item { margin-left: 10px; }
  .contact-web {
    font-size: 16px;
    color: var(--leaf-green);
    letter-spacing: 0.18em;
    margin-top: 8px;
  }
</style>
</head>
<body>
  <main class="sheet">
    <section class="card card-front" aria-label="Card front">
      <div class="brand-dot" aria-hidden="true"></div>
      <h1 class="brand-name">Verdant Terraces</h1>
    </section>

    <section class="card card-back" aria-label="Card back">
      <div class="brand-dot" aria-hidden="true"></div>
      <div class="rule rule-top"></div>
      <div class="contact">
        <p class="contact-name">Colin Barrow</p>
        <p class="contact-role">Managing Director / Horticulturist</p>
        <p class="contact-lines">
          <span class="item"><span class="label">P:</span> 0481 526 704</span>
          <span class="item"><span class="label">E:</span> colinbarrow@verdantterraces.example.au</span>
        </p>
        <p class="contact-web">verdantterraces.example.au</p>
      </div>
      <div class="rule rule-bottom"></div>
    </section>
  </main>
</body>
</html>
```